Business card design for holistic health care clinic

We need a double-sided business card design for our holistic health care clinic that integrates our logo design and also its color scheme. My business is called Valmira. It is an integrative medicine clinic. You have already done the logo for me. Please ensure an elegant and upscale design that is not cluttered, but still has all the necessary information (please see below for details).

Target Market(s)

Wellness, fitness, rehabilitation for educated, well-traveled open-minded clients who are focused on natural, organic, balanced and preventive healthcare and lifestyle.

Industry/Entity Type

Medical

Contact Information for Business Card

Modern, clean.

Number of Pages Required

1 page

Font styles to use
Serif
Sans Serif

Colors

Designer to choose colors to be used in the design.

Requirements
Must have
• Logo on one side, all other information on the other side.
• Other information should include:
• Tobias Wrenfeld - DOE, CPT, LMT
• 4100 East Marrow Drive
• Austin, TX 78119
• 512 555 0148
• 818 555 0192
• info@ValmiraHealth.example
• t.wrenfeld@ValmiraHealth.example
Nice to have
• Darker background on front - but not totally black - shaded/dark gray.

```html
<!DOCTYPE html>
<html lang="en">
<head>
<meta charset="utf-8">
<title>Valmira – Business Card</title>
<link href="https://fonts.googleapis.com/css2?family=Nunito:wght@600;700&family=Work+Sans:wght@300;400;600&display=swap" rel="stylesheet">
<style>
  :root {
    --brand-blue: #1a93d3;
    --card-white: #ffffff;
    --card-dark: #2a2a2b;
    --backdrop: #1c1c1d;
    --text-gray: #4a4a4a;
  }
  * { margin: 0; padding: 0; box-sizing: border-box; }
  html, body {
    width: 1200px; height: 930px; overflow: hidden;
    background: var(--backdrop);
  }
  .card {
    position: absolute; top: 293px;
    width: 540px; height: 309px; overflow: hidden;
  }
  .card--back { left: 42px; background: var(--card-white); }
  .card--front { left: 612px; background: var(--card-dark); }

  .brand-name {
    position: absolute;
    font-family: "Nunito", sans-serif; font-weight: 700;
    color: var(--brand-blue); letter-spacing: 1px; line-height: 1;
  }
  .brand-tagline {
    position: absolute;
    font-family: "Nunito", sans-serif; font-weight: 600;
    color: var(--brand-blue); line-height: 1; white-space: nowrap;
  }
  .card--back .brand-name { left: 30px; top: 52px; font-size: 44px; }
  .card--back .brand-tagline { left: 33px; top: 101px; font-size: 13.5px; }
  .card--front .brand-name { right: 28px; top: 224px; font-size: 50px; }
  .card--front .brand-tagline { right: 29px; top: 267px; font-size: 15.5px; }

  .staff-band {
    position: absolute; top: 0; bottom: 0; width: 14px;
    background: var(--brand-blue);
  }
  .card--back .staff-band { right: 0; }
  .card--front .staff-band { left: 0; width: 18px; }

  .person-name {
    position: absolute; left: 30px; top: 155px;
    font-family: "Work Sans", sans-serif; font-weight: 600;
    font-size: 25px; letter-spacing: -0.5px; color: var(--brand-blue);
    text-transform: uppercase; line-height: 1;
  }
  .person-credentials {
    position: absolute; left: 31px; top: 183px;
    font-family: "Work Sans", sans-serif; font-weight: 400;
    font-size: 13px; color: var(--text-gray); line-height: 1;
  }
  .divider {
    position: absolute; left: 30px; top: 200px;
    width: 473px; height: 1.5px; background: var(--brand-blue);
  }
  .contact-list {
    position: absolute; left: 30px; top: 220px; list-style: none;
    font-family: "Work Sans", sans-serif; font-weight: 300;
    font-size: 14px; color: var(--text-gray);
  }
  .contact-list li {
    display: flex; align-items: center; height: 16.8px;
  }
  .contact-list svg { width: 9px; height: 9px; margin-right: 10px; flex: none; }
  .address {
    position: absolute; right: 37px; top: 254px; text-align: right;
    font-family: "Work Sans", sans-serif; font-weight: 300;
    font-size: 14px; line-height: 16.8px; color: var(--text-gray);
  }
</style>
</head>
<body>

<section class="card card--back" aria-label="Business card, contact side">
  <div class="brand-name">VALMIRA</div>
  <div class="brand-tagline">Integrative Holistic Medicine</div>

  <div class="person-name">Tobias Wrenfeld</div>
  <div class="person-credentials">DOE, CPT, LMT</div>
  <div class="divider"></div>

  <ul class="contact-list">
    <li>
      <svg viewBox="0 0 10 10" aria-hidden="true"><path d="M2 0.5 L3.6 2.8 L2.8 3.8 Q4 6.4 6.2 7.2 L7.2 6.4 L9.5 8 L8.4 9.6 Q2.5 9 0.4 1.6 Z" fill="var(--brand-blue)"/></svg>
      512 555 0148
    </li>
    <li>
      <svg viewBox="0 0 10 10" aria-hidden="true"><rect x="2.5" y="0.5" width="5" height="9" rx="1" fill="none" stroke="var(--brand-blue)" stroke-width="1.4"/><rect x="4.3" y="7.2" width="1.4" height="1" fill="var(--brand-blue)"/></svg>
      818 555 0192
    </li>
    <li>
      <svg viewBox="0 0 10 10" aria-hidden="true"><rect x="0.7" y="2" width="8.6" height="6" fill="none" stroke="var(--brand-blue)" stroke-width="1.2"/><path d="M0.7 2 L5 5.6 L9.3 2" fill="none" stroke="var(--brand-blue)" stroke-width="1.2"/></svg>
      info@ValmiraHealth.example
    </li>
    <li>
      <svg viewBox="0 0 10 10" aria-hidden="true"><circle cx="5" cy="5" r="4.3" fill="none" stroke="var(--brand-blue)" stroke-width="1.1"/><ellipse cx="5" cy="5" rx="1.8" ry="4.3" fill="none" stroke="var(--brand-blue)" stroke-width="0.9"/><path d="M0.7 5 H9.3 M1.5 2.8 H8.5 M1.5 7.2 H8.5" stroke="var(--brand-blue)" stroke-width="0.8"/></svg>
      t.wrenfeld@ValmiraHealth.example
    </li>
  </ul>

  <div class="address">4100 East Marrow Drive<br>Austin, TX 78119</div>

  <div class="staff-band"></div>
</section>

<section class="card card--front" aria-label="Business card, brand side">
  <div class="staff-band"></div>
  <div class="brand-name">VALMIRA</div>
  <div class="brand-tagline">Integrative Holistic Medicine</div>
</section>

</body>
</html>
```